Zelvo Stationary

Design the stationary of Zelvo Promotions Group.

Zelvo is a BTL company, BTL meaning "below the line". In other words Zelvo is a Promotional Marketing company (the company that design the brands promotional activities).

The design should transmit creativity, agility, boldness.

I need:
* Bis Card
* Letter head
* Envelopes, both vertical and horizontal (for legal size), and letter envelope
* Folders
* PPT template (Title page and regular page)
* CD slip (CD envelope)
* ID card (employee card)

And what ever else you want to throw in.
Updates

Guys,

Something I missed from the brief.   The predominat color should be RED.

Also, have fun and play with the exclamation mark (!) of the logo. 

Hi guys, more comments:

Remember that Zelvo is a "creativity" agency, not in the advertising side but on the promotional side, and that should reflect on the stationary.

 I want a bold design.  Bold and yet crisp.

 

Guys, i just uploaded the Logo in AI format.

I Also uploaded the actual Zelvo Bis Card, wich I like.  So I will like to see some designs with that bis card approach.

Guys, I am so sorry, but I notice in your last post that I upladed a wrong design ("13154_promotions_group_zelvo_brief225630.ai").  The problem was that I asked the designer the file in AI format and he send me thw wrong file, and since I dont have Illustrator I could not verify it.

The differences are minor, I just already ask him the correct one (similar to the EPS file).

Sorry                                   

Just post the correct AI file : "Zelvo Logo.ai"

Reason: I'm expecting more designs to choose from and also I wont be available tomorrow to decide.

Reason: Sorry guys, but we are not there yet!

Target Market(s)

Marketing directors, Marketing Managers

Industry/Entity Type

Legal

Requirements
Must have
• Must work with the logo attached.
The predominat color should be RED.
Play and have fun with the exclamation mark (!).
Should not have
• * No old fonts

Should not be:
* boring
* Informal
* rigid

```html
<!DOCTYPE html>
<html lang="en">
<head>
<meta charset="utf-8">
<title>Zelvo Promotions Group — Stationery</title>
<link rel="stylesheet" href="https://fonts.googleapis.com/css2?family=Open+Sans:wght@400;600;800&display=swap">
<style>
  :root{
    --red:#c8141f;
    --red-dark:#8e0c14;
    --black:#161616;
    --charcoal:#242424;
    --paper:#ffffff;
    --ink:#333333;
    --muted:#8a8a8a;
    --stage:#3a3a3a;
  }
  *{box-sizing:border-box;margin:0;padding:0}
  html,body{width:1200px;height:589px;overflow:hidden}
  body{background:var(--stage);font-family:"Open Sans",Arial,sans-serif;position:relative}
  .piece{position:absolute;overflow:hidden;box-shadow:0 6px 18px rgba(0,0,0,.45)}
  .wordmark{display:flex;align-items:center;gap:5px;font-weight:800;letter-spacing:-.5px;line-height:1}
  .wordmark .dot{width:.45em;height:.45em;border-radius:50%;background:var(--red)}
  .wordmark.on-dark{color:#fff}
  .wordmark.on-light{color:var(--black)}
  .band{position:absolute;left:0;right:0;background:var(--red);color:#fff;font-size:7px;display:flex;align-items:center;gap:14px;padding:0 14px}
  .accent-circle{position:absolute;border-radius:50%;background:var(--red)}

  /* Letterhead */
  .letterhead{left:24px;top:24px;width:300px;height:541px;background:var(--paper);color:var(--ink);padding:26px 24px;font-size:7px;line-height:1.55}
  .letterhead .wordmark{font-size:24px}
  .letterhead .contact{position:absolute;right:22px;top:30px;text-align:left;font-size:6.5px;color:var(--muted);line-height:1.5}
  .letterhead .body{margin-top:42px}
  .letterhead .body p{margin-bottom:9px}
  .letterhead ul{margin:0 0 9px 14px}
  .signature{width:90px;height:26px;margin:6px 0 2px;background:linear-gradient(90deg,#e4e4e4,#f6f6f6)}
  .letterhead .footer-band{position:absolute;left:0;right:0;bottom:0;height:10px;background:var(--red)}

  /* Horizontal envelope */
  .envelope-h{left:210px;top:160px;width:400px;height:220px;background:var(--black)}
  .envelope-h .flap{position:absolute;left:0;top:0}
  .envelope-h .wordmark{position:absolute;left:22px;top:82px;font-size:28px}
  .envelope-h .band{bottom:40px;height:20px}
  .envelope-h .accent-circle{right:36px;top:90px;width:70px;height:70px}

  /* Folder */
  .folder{left:650px;top:20px;width:520px;height:300px;background:var(--charcoal)}
  .folder .wordmark{position:absolute;left:26px;top:30px;font-size:34px}
  .folder .band{bottom:56px;height:22px}
  .folder .accent-circle{right:24px;bottom:20px;width:60px;height:60px}

  /* ID card */
  .id-card{left:990px;top:46px;width:112px;height:168px;background:var(--paper);border-radius:6px;color:var(--ink);padding:20px 9px 0}
  .id-card::before{content:"";position:absolute;left:44px;top:6px;width:24px;height:5px;border-radius:3px;background:#bbb}
  .id-card .wordmark{font-size:17px}
  .id-card dl{margin-top:10px;font-size:5.5px;line-height:1.7;color:var(--muted)}
  .id-card .portrait{position:absolute;left:32px;top:88px;width:48px;height:48px;border-radius:50%;background:radial-gradient(circle,#e9c6b4,#a8786a);border:2px solid var(--red)}
  .id-card .name-bar{position:absolute;left:0;right:0;bottom:0;height:22px;background:var(--red);color:#fff;font-size:7px;font-weight:600;display:flex;align-items:center;justify-content:center}

  /* Business cards */
  .biz-front{left:640px;top:340px;width:160px;height:92px;background:var(--paper);color:var(--ink);padding:14px 12px}
  .biz-front .wordmark{font-size:20px}
  .biz-front .details{margin-top:14px;font-size:5.5px;color:var(--muted);line-height:1.6}
  .biz-front .accent-circle{right:12px;top:14px;width:22px;height:22px}
  .biz-back{left:640px;top:450px;width:160px;height:92px;background:var(--black)}
  .biz-back .wordmark{position:absolute;left:14px;top:22px;font-size:22px}
  .biz-back .band{bottom:14px;height:12px}

  /* Vertical legal envelope */
  .envelope-v{left:430px;top:395px;width:150px;height:180px;background:var(--black)}
  .envelope-v .wordmark{position:absolute;left:14px;top:18px;font-size:18px}
  .envelope-v .band{bottom:24px;height:14px;font-size:5.5px;gap:8px;padding:0 10px}
  .envelope-v .accent-circle{right:18px;top:70px;width:44px;height:44px}

  /* CD slip */
  .cd-slip{left:840px;top:340px;width:150px;height:230px;background:var(--charcoal)}
  .cd-slip .accent-circle{left:45px;top:40px;width:60px;height:60px}
  .cd-slip .tagline{position:absolute;left:14px;top:140px;color:#fff;font-size:9px;letter-spacing:.5px}
  .cd-slip .wordmark{position:absolute;left:14px;top:165px;font-size:20px}
  .cd-slip .band{bottom:16px;height:12px}

  /* CD */
  .cd{left:1008px;top:396px;width:172px;height:172px;border-radius:50%;background:var(--black)}
  .cd .label-half{position:absolute;right:0;top:0;width:86px;height:172px;background:var(--red)}
  .cd .wordmark{position:absolute;left:18px;top:76px;font-size:16px}
  .cd .hole{position:absolute;left:72px;top:72px;width:28px;height:28px;border-radius:50%;background:var(--stage);border:6px solid #ddd}
</style>
</head>
<body>

  <section class="piece letterhead">
    <div class="wordmark on-light">zelvo<span class="dot"></span></div>
    <div class="contact">P.O. Box 48210 Harbor City, 30418<br>+1 (555) 014-2290<br>+1 (555) 014-2291<br>www.zelvo.com</div>
    <div class="body">
      <p>Dear Mr. First Last</p>
      <p>We are pleased to share our plan for the spring campaign and the launch events across all regions this season.</p>
      <p>Our team brings fresh ideas, fast delivery and bold shelf presence to every brand we serve.</p>
      <p>Qualifications:</p>
      <ul><li>field team lead</li><li>event staffing plan</li><li>retail display kit</li></ul>
      <p>Results come from bold ideas put into motion with care.</p>
      <p>Sincerely</p>
      <div class="signature" role="img" aria-label="Handwritten signature"></div>
      <p>Dana Merrow</p>
    </div>
    <div class="footer-band"></div>
  </section>

  <section class="piece envelope-h">
    <svg class="flap" width="400" height="70" viewBox="0 0 400 70" aria-hidden="true">
      <path d="M0 0H400V40L360 70H40L0 40Z" fill="#c8141f"/>
      <circle cx="200" cy="44" r="5" fill="none" stroke="#fff" stroke-width="1.5"/>
      <line x1="205" y1="44" x2="222" y2="44" stroke="#fff" stroke-width="1.5"/>
    </svg>
    <div class="wordmark on-dark">zelvo<span class="dot"></span></div>
    <div class="accent-circle"></div>
    <div class="band"><span>P.O. Box 48210 Harbor City, 30418</span><span>+1 (555) 014-2290</span><span>www.zelvo.com</span></div>
  </section>

  <section class="piece folder">
    <div class="wordmark on-dark">zelvo<span class="dot"></span></div>
    <div class="band"><span>P.O. Box 48210 Harbor City, 30418</span><span>+1 (555) 014-2290</span><span>www.zelvo.com</span></div>
    <div class="accent-circle"></div>
  </section>

  <section class="piece id-card">
    <div class="wordmark on-light">zelvo<span class="dot"></span></div>
    <dl><dt>Dept: Events</dt><dt>Staff No: 04217</dt><dt>Valid: 12/26</dt></dl>
    <div class="portrait" role="img" aria-label="Employee portrait photograph"></div>
    <div class="name-bar">Lena Ostrova</div>
  </section>

  <section class="piece biz-front">
    <div class="wordmark on-light">zelvo</div>
    <div class="accent-circle"></div>
    <div class="details">Lena Ostrova · Events Director<br>+1 (555) 014-2290 · www.zelvo.com</div>
  </section>

  <section class="piece biz-back">
    <div class="wordmark on-dark">zelvo<span class="dot"></span></div>
    <div class="band"></div>
  </section>

  <section class="piece envelope-v">
    <div class="wordmark on-dark">zelvo<span class="dot"></span></div>
    <div class="accent-circle"></div>
    <div class="band"><span>+1 (555) 014-2290</span><span>www.zelvo.com</span></div>
  </section>

  <section class="piece cd-slip">
    <div class="accent-circle"></div>
    <p class="tagline">YOUR TAGLINE GOES HERE</p>
    <div class="wordmark on-dark">zelvo<span class="dot"></span></div>
    <div class="band"></div>
  </section>

  <section class="piece cd">
    <div class="label-half"></div>
    <div class="wordmark on-dark">zelvo</div>
    <div class="hole"></div>
  </section>

</body>
</html>
```